diamondscoutline.net - Social Media Branding

diamondscoutline.net --> Social Media Re-Branding & Graphics
Facebook: @dmndscoutline - Instagram: @diamondscoutline - Twitter: @dmndscoutline

Looking to find a good designer to help with my diamondscoutline.net social media sites!
- facebook banner
- twitter banner
- instagram template (square and banner size)
- Quote or Information Template
- Committed Template (uniformed) - see the ones I made (& i am no professional) at diamondscoutline.net/committed - needs to have diamondscoutline.net logo, room for: the committed school and the team the player plays on.

Also willing to pay extra for a graphic that is the "complete package" that detail all of the steps of the recruiting process detailed in diamondscoutline.net

Font styles to use
Sans Serif

Colors
ec1f27
fbee3e

```html
<!DOCTYPE html>
<html lang="en">
<head>
<meta charset="utf-8">
<title>diamondscoutline.net – Social Profile Headers</title>
<link href="https://fonts.googleapis.com/css2?family=Barlow:wght@400;500;600&family=Poppins:wght@700&family=Roboto:wght@500;700&display=swap" rel="stylesheet">
<style>
  :root {
    --brand-red: #c41e2e;
    --accent-red: #ec1f27;
    --brand-yellow: #fbee3e;
    --ink: #111111;
    --panel: #f5f4f4;
    --page: #ffffff;
    --photo-dark: #4a4a4a;
    --photo-mid: #8a8a8a;
    --photo-light: #b9b9b9;
    --follow-blue: #1da1f2;
    --tab-blue: #365899;
    --line: #dddfe2;
    --muted: #90949c;
  }
  * { box-sizing: border-box; margin: 0; padding: 0; }
  html, body { width: 1200px; height: 900px; overflow: hidden; background: var(--page); }
  body { position: relative; font-family: "Barlow", sans-serif; color: var(--ink); }

  .profile-card {
    position: absolute; left: 129px; width: 943px; background: var(--page);
    box-shadow: 0 8px 18px rgba(0,0,0,.28);
  }
  .profile-card--short { top: 84px; height: 417px; }
  .profile-card--full { top: 541px; height: 274px; }

  .cover { position: absolute; left: 0; top: 0; width: 943px; background: var(--panel); overflow: hidden; }
  .profile-card--short .cover { height: 315px; }
  .profile-card--full .cover { height: 228px; }
  .cover-art { position: absolute; left: 0; top: 0; }

  .brand-block { position: absolute; text-align: center; transform: translateX(-50%); }
  .brand-dot { display: block; margin: 0 auto; border-radius: 50%; background: var(--brand-red); }
  .brand-name { font-family: "Poppins", sans-serif; font-weight: 700; color: var(--ink); white-space: nowrap; line-height: 1; }
  .tagline { font-weight: 400; white-space: nowrap; }
  .join-button {
    display: inline-block; background: var(--brand-red); color: var(--brand-yellow);
    font-weight: 600; letter-spacing: .12em;
  }

  /* short header */
  .profile-card--short .brand-block { left: 724px; top: 20px; }
  .profile-card--short .brand-dot { width: 54px; height: 54px; margin-bottom: 18px; }
  .profile-card--short .brand-name { font-size: 25px; }
  .profile-card--short .tagline { font-size: 15.5px; margin-top: 30px; }
  .profile-card--short .join-button { font-size: 15px; width: 124px; height: 32px; line-height: 32px; margin-top: 12px; }

  .social-row { position: absolute; top: 251px; left: 0; width: 943px; }
  .social-item { position: absolute; transform: translateX(-50%); text-align: center; font-size: 14px; }
  .social-icon { display: block; margin: 0 auto 5px; width: 22px; height: 22px; border-radius: 50%; border: 1.5px solid var(--tab-blue); }
  .social-item:nth-child(1) { left: 588px; }
  .social-item:nth-child(2) { left: 724px; }
  .social-item:nth-child(3) { left: 863px; }

  .avatar {
    position: absolute; border-radius: 50%; background: var(--page);
    border: 1.5px solid #e4e4e4; display: flex; align-items: center; justify-content: center;
  }
  .avatar-name { font-family: "Poppins", sans-serif; font-weight: 700; color: var(--brand-red); }
  .profile-card--short .avatar { left: 30px; top: 195px; width: 206px; height: 206px; }
  .profile-card--short .avatar-name { font-size: 16px; }

  .follow-button {
    position: absolute; left: 792px; top: 327px; width: 122px; height: 60px;
    border: 2px solid var(--follow-blue); border-radius: 30px; color: var(--follow-blue);
    font-family: "Roboto", sans-serif; font-weight: 700; font-size: 23px;
    display: flex; align-items: center; justify-content: center;
  }

  /* full header */
  .profile-card--full .brand-block { left: 642px; top: 22px; }
  .profile-card--full .brand-dot { width: 40px; height: 40px; margin-bottom: 14px; }
  .profile-card--full .brand-name { font-size: 19px; }
  .profile-card--full .tagline { font-size: 11.5px; margin-top: 22px; }
  .profile-card--full .join-button { font-size: 10.5px; width: 87px; height: 21px; line-height: 21px; margin-top: 8px; }

  .social-list { position: absolute; left: 780px; top: 68px; list-style: none; font-size: 10px; }
  .social-list li { display: flex; align-items: center; height: 25px; }
  .social-list .social-icon { width: 15px; height: 15px; margin: 0 8px 0 0; border-width: 1px; }

  .profile-card--full .avatar { left: 20px; top: 72px; width: 182px; height: 182px; z-index: 2; }
  .profile-card--full .avatar-name { font-size: 14px; }

  .admin-actions { position: absolute; top: 181px; font-family: "Roboto", sans-serif; font-weight: 500; font-size: 13px; color: #4b4f56; }
  .action-button {
    position: absolute; top: 0; height: 28px; background: var(--page); border: 1px solid var(--line);
    display: flex; align-items: center; justify-content: center; gap: 6px; white-space: nowrap;
  }
  .badge { background: #e02f2f; color: #fff; font-size: 10px; padding: 1px 4px; border-radius: 2px; }
  .action-button--update { left: 626px; width: 116px; }
  .action-button--log { left: 765px; width: 121px; }
  .action-button--more { left: 886px; width: 39px; color: var(--muted); letter-spacing: 1px; }

  .tab-bar {
    position: absolute; left: 0; top: 228px; width: 943px; height: 46px; display: flex; padding-left: 223px;
    font-family: "Roboto", sans-serif; font-weight: 500; font-size: 16px; color: var(--tab-blue);
  }
  .tab { display: flex; align-items: center; justify-content: center; gap: 5px; border-left: 1px solid var(--line); }
  .tab:last-child { border-right: 1px solid var(--line); }
  .tab-count { font-size: 12px; color: var(--muted); font-weight: 400; }
  .caret { width: 0; height: 0; border-left: 4px solid transparent; border-right: 4px solid transparent; border-top: 5px solid var(--tab-blue); }
</style>
</head>
<body>

<section class="profile-card profile-card--short">
  <div class="cover">
    <svg class="cover-art" width="943" height="315" viewBox="0 0 943 315">
      <defs>
        <linearGradient id="photoToneA" x1="0" y1="0" x2="1" y2="1">
          <stop offset="0" stop-color="var(--photo-mid)"/>
          <stop offset=".55" stop-color="var(--photo-dark)"/>
          <stop offset="1" stop-color="var(--photo-light)"/>
        </linearGradient>
      </defs>
      <path role="img" aria-label="Black and white photo of a softball catcher in red chest protector holding a red helmet, with a yellow ball in flight" d="M0 0 H463 A182 182 0 0 1 437 315 H0 Z" fill="url(#photoToneA)"/>
      <path d="M463 0 A182 182 0 0 1 437 315" fill="none" stroke="var(--brand-red)" stroke-width="10"/>
    </svg>
    <div class="brand-block">
      <span class="brand-dot"></span>
      <p class="brand-name">diamondscoutline.net</p>
      <p class="tagline">Learn the Step-by-Step Recruiting Process!</p>
      <span class="join-button">JOIN TODAY</span>
    </div>
    <div class="social-row">
      <div class="social-item"><span class="social-icon"></span>@dmndscoutline</div>
      <div class="social-item"><span class="social-icon"></span>@diamondscoutline</div>
      <div class="social-item"><span class="social-icon"></span>@dmndscoutline</div>
    </div>
  </div>
  <div class="avatar"><span class="avatar-name">diamondscoutline.net</span></div>
  <div class="follow-button">Follow</div>
</section>

<section class="profile-card profile-card--full">
  <div class="cover">
    <svg class="cover-art" width="943" height="228" viewBox="0 0 943 228">
      <defs>
        <linearGradient id="photoToneB" x1="0" y1="0" x2="1" y2="1">
          <stop offset="0" stop-color="var(--photo-mid)"/>
          <stop offset=".55" stop-color="var(--photo-dark)"/>
          <stop offset="1" stop-color="var(--photo-light)"/>
        </linearGradient>
      </defs>
      <path role="img" aria-label="Black and white photo of a softball catcher in red gear holding a red helmet, with a yellow ball in flight" d="M0 0 H446 A150 150 0 0 1 436 228 H0 Z" fill="url(#photoToneB)"/>
      <path d="M446 0 A150 150 0 0 1 436 228" fill="none" stroke="var(--brand-red)" stroke-width="8"/>
    </svg>
    <div class="brand-block">
      <span class="brand-dot"></span>
      <p class="brand-name">diamondscoutline.net</p>
      <p class="tagline">Learn the Step-by-Step Recruiting Process!</p>
      <span class="join-button">JOIN TODAY</span>
    </div>
    <ul class="social-list">
      <li><span class="social-icon"></span>@dmndscoutline</li>
      <li><span class="social-icon"></span>@diamondscoutline</li>
      <li><span class="social-icon"></span>@dmndscoutline</li>
    </ul>
    <div class="admin-actions">
      <div class="action-button action-button--update">Update Info <span class="badge">3</span></div>
      <div class="action-button action-button--log">
        <svg width="14" height="12" viewBox="0 0 14 12" aria-hidden="true"><g fill="#4b4f56"><rect x="0" y="0" width="2" height="2"/><rect x="0" y="5" width="2" height="2"/><rect x="0" y="10" width="2" height="2"/><rect x="4" y="0.5" width="10" height="1"/><rect x="4" y="5.5" width="10" height="1"/><rect x="4" y="10.5" width="10" height="1"/></g></svg>
        Activity Log
      </div>
      <div class="action-button action-button--more">•••</div>
    </div>
  </div>
  <div class="avatar"><span class="avatar-name">diamondscoutline.net</span></div>
  <nav class="tab-bar">
    <div class="tab" style="width:118px">Timeline <span class="caret"></span></div>
    <div class="tab" style="width:84px">About</div>
    <div class="tab" style="width:115px">Friends <span class="tab-count">14</span></div>
    <div class="tab" style="width:91px">Photos</div>
    <div class="tab" style="width:118px">
      <svg width="11" height="13" viewBox="0 0 11 13" aria-hidden="true"><path d="M2.5 6 V4 a3 3 0 0 1 6 0 V6" fill="none" stroke="var(--tab-blue)" stroke-width="1.6"/><rect x="0" y="6" width="11" height="7" rx="1" fill="var(--tab-blue)"/></svg>
      Archive
    </div>
    <div class="tab" style="width:94px">More <span class="caret"></span></div>
  </nav>
</section>

</body>
</html>
```